Customer Paperwork Redesign

We need the following PDF redesigned to be more user friendly.
We are finding that
1. People are not setting up payments
2. People are not returning the paperwork with the bank information properly filled out.
3. The bank details are actually not used, they are only a backup. This needs to be made prominent. many people phone us about this.
4. People find it all too confusing. Perosnally i think its easy but hey.. im not our customer.
Let me know what you can do!
Content can be totaly rewritten,
This form gets automatically filled out by our software, printed and then mailed to them. They only need to sign, and fill out the bank details and return it. They also need to call up to setup payments.
The final paylinko form can be redesigned however, how too much. eg, Locations of content should be fairly much the same.
Current document is attached. its the PDF.
I have also uploaded a logo, and a .doc which is handy to edit. Also have uploaded the paylinko PDF too.
Target Market(s)
Our target market is people who dont have very good english skills, cant read well and need something really easy and simple to follow. Something thats to much effort becomes too hard
Industry/Entity Type
Bank
Look and feel
Each slider illustrates characteristics of the customer's brand and the style your logo design should communicate.

```html
<!DOCTYPE html>
<html lang="en">
<head>
<meta charset="utf-8">
<title>Terms of Contract Agreement</title>
<link rel="stylesheet" href="https://fonts.googleapis.com/css2?family=PT+Serif:wght@400;700&family=Roboto:wght@400;500&display=swap">
<style>
  :root {
    --lime: #b8ea3c;
    --panel: #e4ecef;
    --ink: #1f1f1f;
    --title: #2a2a2a;
    --band-text: #1f6a12;
    --brand: #3a3f44;
    --brand-mark: #38b8e0;
  }
  html, body { margin: 0; padding: 0; overflow: hidden; }
  body { width: 852px; height: 1200px; background: var(--lime); font-family: "PT Serif", Georgia, serif; color: var(--ink); position: relative; }
  .page {
    position: absolute; left: 8px; top: 8px; width: 836px; height: 1150px;
    background: #fff;
  }
  .brand {
    position: absolute; right: 18px; top: 14px;
    display: flex; align-items: center; gap: 8px;
    font-family: "Roboto", Arial, sans-serif; font-weight: 500; font-size: 15px;
    color: var(--brand); letter-spacing: .5px;
  }
  .brand-mark { width: 20px; height: 20px; background: var(--brand-mark); }
  .doc-title {
    position: absolute; top: 50px; left: 0; width: 100%; margin: 0;
    text-align: center; font-family: "Roboto", Arial, sans-serif; font-weight: 400;
    font-size: 19px; letter-spacing: .3px; color: var(--title);
  }
  .terms {
    position: absolute; left: 26px; top: 82px; width: 788px; height: 1062px;
    background: var(--panel); border-radius: 10px; box-sizing: border-box;
    padding: 16px 30px 18px 18px; margin: 0; list-style: none; counter-reset: clause;
    display: flex; flex-direction: column; justify-content: space-between;
  }
  .terms li {
    position: relative; padding-left: 32px;
    font-size: 17px; line-height: 24px;
    counter-increment: clause;
  }
  .terms li::before { content: counter(clause); position: absolute; left: 0; top: 0; font-weight: 700; }
  .keep-note {
    position: absolute; left: 0; top: 1160px; width: 852px; text-align: center;
    font-family: "Roboto", Arial, sans-serif; font-size: 20px; color: var(--band-text);
    letter-spacing: .3px;
  }
</style>
</head>
<body>
<div class="page">
  <div class="brand"><span class="brand-mark"></span>TECHSHARE RENTALS</div>
  <h1 class="doc-title">TERMS OF CONTRACT AGREEMENT</h1>
  <ol class="terms">
    <li>You are renting a computer from us. The computer is listed in the First Schedule of this agreement. You have checked the computer and you are happy with it. You did not sign because of any promise that is not written in this agreement.</li>
    <li>The rent is shown in the First Schedule. You pay it every month, before the month starts. The first payment is on the start date. You allow Benefitlink and/or the Department of Community Support to pay your rent to us from your benefit. You must still pay the rent, even if you and we disagree about something.</li>
    <li>You must make every payment shown in the Schedule, on the date shown.</li>
    <li>We own the computer until the rental ends. When the rental ends and every payment is made, the computer becomes yours.</li>
    <li>If your Benefitlink payment stops, all the rent you still owe must be paid straight away. You must pay it within 14 days from the day your benefit stopped.</li>
    <li>If clause 5 happens, the computer does not become yours until every payment is made.</li>
    <li>You can keep and use the computer in peace for the whole rental, as long as you pay the rent on time.</li>
    <li>You promise that you are allowed to sign this agreement. You promise the information you gave us is true and complete. If you do not pay on time, we can take the computer back, with or without telling you first, and this agreement ends. Taking the computer back does not end your payments. You must still pay everything you owe. If the computer is damaged, we may also ask you to pay for the repair. We may take any action we need to get back the unpaid money or the repair cost.</li>
    <li>If the law says tax or stamp duty must be paid, we will tell you how much. You pay it to us with your first rent payment. We then pay it to the government.</li>
    <li>We asked you to get legal advice about this agreement. It was your choice to do this or not. You signed this agreement freely. Nobody forced you. You understand this agreement, with or without legal advice.</li>
    <li>In this agreement, one person can also mean many people, and "she" can also mean "he", and the other way around.</li>
  </ol>
</div>
<div class="keep-note">YOU KEEP THIS PAGE BACK</div>
</body>
</html>
```